Board Presentation template

Design a simple and clean PowerPoint slide templates for a Board meeting. The slides should have predominantly white backgrounds and use the colors of our Logo (attached): Tones of grey and orange and blue.
The company name is called Keystone Lane Gauging.
It sell, calibrate, service and repair industrial and commercial scales of all types. In particular, Truck scales, floor scales, counting scales and benchtop scales.
There is no website for Keystone Lane Gauging, but we have three affiliates that have their own websites:
https://www.fernwaybalance.example/
https://meadowlarkhandlingandmassing.example/
https://tvbalance.example/
Target Market(s)
Industrial and Commercial Weighing systems
Industry/Entity Type
Look and feel

```html
<!DOCTYPE html>
<html lang="en">
<head>
<meta charset="utf-8">
<title>Keystone Lane Gauging – Board Presentation</title>
<link href="https://fonts.googleapis.com/css2?family=Oswald:wght@500;600&family=Inter:wght@400;500;600&display=swap" rel="stylesheet">
<style>
:root{
  --canvas:#7a7879;
  --paper:#ffffff;
  --red:#c0272d;
  --ink:#2f3238;
  --dark:#3a3f47;
  --text:#3d3d3d;
  --card-top:#ffffff;
  --card-bottom:#f6e1e2;
}
*{margin:0;padding:0;box-sizing:border-box}
html,body{width:1029px;height:1200px;overflow:hidden;background:var(--canvas)}
body{position:relative;font-family:"Inter",sans-serif;color:var(--text)}
.slide{position:absolute;width:458px;height:258px;background:var(--paper);overflow:hidden;border-bottom:2px solid var(--dark)}
.col-left{left:39px}.col-right{left:533px}
.row-1{top:41px}.row-2{top:328px}.row-3{top:614px}.row-4{top:901px}
.slide-title{position:absolute;left:0;top:10px;width:295px;height:24px;background:var(--red);border-radius:0 12px 12px 0;
  color:#fff;font-family:"Oswald",sans-serif;font-weight:600;font-size:15px;line-height:24px;padding-left:23px;letter-spacing:.1px;text-transform:uppercase}
.page-tab{position:absolute;right:0;bottom:0;width:110px;height:20px;background:var(--dark);clip-path:polygon(13px 0,100% 0,100% 100%,0 100%);
  color:#fff;font-size:8px;font-weight:600;line-height:20px;text-align:right;padding-right:24px}
.photo{position:absolute;border:2px solid #fff;border-radius:12px;box-shadow:0 0 4px rgba(0,0,0,.25)}
.abs{position:absolute}
.tick{position:relative;padding-left:17px;font-size:8px;line-height:1}
.tick::before{content:"";position:absolute;left:0;top:0;width:6px;height:6px;border:1px solid #555;border-radius:1px}
.tick::after{content:"";position:absolute;left:2px;top:-1px;width:3px;height:6px;border:solid #555;border-width:0 1.3px 1.3px 0;transform:rotate(40deg)}
.tick.red::before{border-color:var(--red)}
.tick.red::after{border-color:var(--red)}
.pos{position:absolute}
/* cover */
.cover-brand{position:absolute;left:318px;top:168px;width:130px;text-align:center}
.cover-brand .mark{width:26px;height:26px;border:3px solid var(--ink);border-radius:50%;margin:0 auto 8px}
.cover-brand .name{font-family:"Oswald",sans-serif;font-weight:600;font-size:14px;line-height:16px;color:var(--ink);text-transform:uppercase}
/* about */
.about-text{position:absolute;left:30px;top:55px;width:177px;font-size:8px;line-height:13.9px;text-align:justify}
.about-text p+p{margin-top:13.9px}
/* intro */
.icon-ring{position:absolute;width:27px;height:27px;border:1.3px solid var(--ink);border-radius:50%}
.icon-ring::after{content:"";position:absolute;left:7px;top:7px;width:10px;height:10px;border:1.3px solid var(--red);border-radius:50%}
.label{font-family:"Oswald",sans-serif;font-weight:500;font-size:9.5px;color:var(--ink);text-transform:uppercase}
.stack .tick{display:block;margin-bottom:9.5px}
.agenda{list-style:none;font-size:8px;line-height:16.5px}
.agenda b{display:inline-block;width:18px;font-weight:600}
/* highlights */
.lead{position:absolute;left:48px;top:48px;width:362px;text-align:center;font-size:8px;line-height:13px}
.metric{position:absolute;width:100px;text-align:center;font-size:8.5px;line-height:12px;color:var(--ink)}
.metric .ring{width:72px;height:72px;border:1.5px solid var(--ink);border-radius:50%;margin:0 auto 10px;display:flex;align-items:center;justify-content:center}
.metric strong{font-weight:500;display:block}
/* market */
.section-tab{position:absolute;left:0;height:15px;background:var(--dark);color:#fff;font-size:7.4px;font-weight:600;line-height:15px;padding-left:36px;
  clip-path:polygon(0 0,100% 0,calc(100% - 8px) 100%,0 100%)}
.section-tab::before{content:"";position:absolute;left:25px;top:5px;width:6px;height:5px;border:1px solid #fff;border-radius:50%}
.check-grid{position:absolute;left:37px;top:222px;display:grid;grid-template-columns:112px auto;row-gap:8px}
/* affiliates */
.affiliate{position:absolute;top:59px;width:130px;height:166px;border-radius:10px;background:linear-gradient(var(--card-top),var(--card-bottom));
  box-shadow:0 1px 5px rgba(0,0,0,.12);text-align:center;padding:20px 10px 0}
.affiliate .name{font-family:"Oswald",sans-serif;font-weight:600;font-size:12px;line-height:14px;color:var(--red);text-transform:uppercase;height:60px;display:flex;align-items:center;justify-content:center;flex-direction:column}
.affiliate .name.compact{font-size:10px;line-height:12px;height:30px;white-space:nowrap;margin-bottom:12px}
.affiliate p{font-size:5px;line-height:9px;color:#444}
.affiliate p+p{margin-top:9px}
</style>
</head>
<body>

<!-- 01 Cover -->
<section class="slide col-left row-1">
  <svg class="abs" width="458" height="258" viewBox="0 0 458 258" aria-hidden="true">
    <polygon points="0,187 0,258 130,258" fill="#c0272d"/>
  </svg>
  <div class="abs" role="img" aria-label="Close-up of industrial pressure gauges and steel piping" style="left:0;top:0;width:458px;height:258px;background:linear-gradient(135deg,#c9ced3,#6f7780 45%,#2e343b);clip-path:polygon(0 0,100% 0,100% 46%,124px 255px,0 183px)"></div>
  <div class="cover-brand">
    <div class="mark"></div>
    <div class="name">Keystone Lane<br>Gauging</div>
  </div>
</section>

<!-- 02 Introduction -->
<section class="slide col-left row-2">
  <div class="slide-title">Introduction</div>
  <div class="icon-ring" style="left:24px;top:65px"></div>
  <div class="abs" style="left:67px;top:63px">
    <div class="label">Purpose</div>
    <div class="stack" style="margin-top:6px">
      <span class="tick">Sed ut perspiciatis un</span>
      <span class="tick">Ut enim ad minima</span>
      <span class="tick">Nor again is anyone</span>
    </div>
  </div>
  <div class="icon-ring" style="left:24px;top:146px"></div>
  <div class="abs" style="left:67px;top:145px">
    <div class="label">Goal</div>
    <div class="stack" style="margin-top:6px">
      <span class="tick">Sed ut perspiciatis un</span>
      <span class="tick">Ut enim ad minima</span>
      <span class="tick">Nor again is anyone</span>
    </div>
  </div>
  <div class="photo" role="img" aria-label="Gas meter mounted on a house wall" style="left:180px;top:60px;width:118px;height:170px;background:linear-gradient(160deg,#d8dde0,#9aa5ad 60%,#5f6e78)"></div>
  <div class="icon-ring" style="left:316px;top:60px"></div>
  <div class="abs" style="left:314px;top:92px">
    <div class="label">Agenda</div>
    <ol class="agenda" style="margin-top:1px">
      <li><b>01)</b> Company Overview</li>
      <li><b>02)</b> Market &amp; Industry Outlook</li>
      <li><b>03)</b> Operational Performance</li>
      <li><b>04)</b> Financial Review</li>
      <li><b>05)</b> Calibration Division Updates</li>
      <li><b>06)</b> Strategic Initiatives</li>
      <li><b>07)</b> 2026 Outlook &amp; Next Steps</li>
    </ol>
  </div>
  <div class="page-tab">Page 02 Of 08</div>
</section>

<!-- 03 Market -->
<section class="slide col-left row-3">
  <div class="slide-title">Market &amp; Industry Overview</div>
  <div class="section-tab" style="top:49px;width:156px">Digital Service Portal Launch</div>
  <div class="abs" style="left:37px;top:80px">
    <div class="tick" style="margin-bottom:7.5px">Industry trend: Digital and IoT-enabled scale systems gaining traction</div>
    <div class="tick" style="margin-bottom:7.5px">Supply chain stabilization post-pandemic</div>
    <div class="tick" style="margin-bottom:7.5px">Increased demand for truck and floor scale recalibrations in logistics and manufacturing</div>
    <div class="tick">Competitive analysis snapshot: show 3–4 main competitors with relative market share</div>
  </div>
  <div class="section-tab" style="top:145px;width:118px">Strategic Initiatives</div>
  <div class="abs" style="left:36px;top:170px;font-size:8px;word-spacing:1px">Fleet Expansion&nbsp;&nbsp;&nbsp;&nbsp;&nbsp;|&nbsp;&nbsp;&nbsp;&nbsp;&nbsp;Affiliate Integration&nbsp;&nbsp;&nbsp;&nbsp;&nbsp;|&nbsp;&nbsp;&nbsp;&nbsp;&nbsp;Sustainability</div>
  <div class="section-tab" style="top:191px;width:149px">Calibration Division Update</div>
  <div class="check-grid">
    <span class="tick">Calibration Volume</span>
    <span class="tick">ISO/IEC 17025 Certification Compliance</span>
    <span class="tick">Truck Scale Repairs</span>
    <span class="tick">Technician Training Hours</span>
  </div>
  <div class="page-tab">Page 03 Of 08</div>
</section>

<!-- 04 Master -->
<section class="slide col-left row-4">
  <div class="slide-title">Master Slide</div>
  <div class="page-tab">Page 04 Of 08</div>
</section>

<!-- 05 About -->
<section class="slide col-right row-1">
  <div class="slide-title">About Keystone Lane Gauging</div>
  <div class="about-text">
    <p>KLG provides comprehensive weighing solutions—sales, calibration, servicing, and repair for industrial and commercial scales, including truck scales, floor scales, counting scales, and benchtop units.</p>
    <p>Nor again is there anyone who loves or pursues or desires to obtain pain of itself, because it is pain, but because occasionally circumstances occur in which toil and pain can procure him some great pleasure. To take a trivial example, which of us ever undertakes laborious physical exercise, except to obtain</p>
  </div>
  <div class="photo" role="img" aria-label="Industrial piping with pressure gauges and valves" style="left:242px;top:62px;width:194px;height:162px;background:linear-gradient(150deg,#e4e7e8,#a9b3b8 50%,#54606a)"></div>
  <div class="page-tab">Page 05 Of 08</div>
</section>

<!-- 06 Highlights -->
<section class="slide col-right row-2">
  <div class="slide-title">Key Highlights (YTD 2025)</div>
  <p class="lead">Nor again is there anyone who loves or pursues or desires to obtain pain of itself, because it is pain, but because occasionally circumstances occur in which toil and pain can procure him some great pleasure. To take a trivial example, which of us ever</p>
  <div class="metric" style="left:18px;top:98px">
    <div class="ring"><svg width="30" height="34" viewBox="0 0 30 34" fill="none" stroke="#c0272d" stroke-width="1.6"><rect x="3" y="5" width="18" height="25" rx="1.5"/><path d="M7 13h9M7 18h9M7 23h6"/><circle cx="22" cy="22" r="5"/><path d="M26 26l3 4"/></svg></div>
    <strong>Service Contracts Renewed:</strong>95% retention rate
  </div>
  <div class="metric" style="left:121px;top:122px">
    <div class="ring"><svg width="36" height="30" viewBox="0 0 36 30" fill="none" stroke="#c0272d" stroke-width="1.6"><circle cx="18" cy="7" r="5"/><path d="M16 7l2 2 3-4"/><path d="M2 17l7-5 6 3 6-3 6 3 7-3M9 12l-2 10 5 4 5-3 5 3 6-6"/></svg></div>
    <strong>New Partnerships</strong>Added 3 regional distributors
  </div>
  <div class="metric" style="left:226px;top:98px">
    <div class="ring"><svg width="36" height="34" viewBox="0 0 36 34" fill="none" stroke="#c0272d" stroke-width="1.6"><path d="M4 32h30M7 32V24h4v8M14 32V20h4v8M21 32V15h4v17M28 32V10h4v22M6 20l8-6 6 3 10-12M26 4h5v5"/></svg></div>
    <strong>Employee Growth:</strong>+12 new technicians
  </div>
  <div class="metric" style="left:332px;top:122px">
    <div class="ring"><svg width="36" height="32" viewBox="0 0 36 32" fill="none" stroke="#c0272d" stroke-width="1.6"><circle cx="10" cy="8" r="5"/><path d="M18 16V11h3v5M23 16V8h3v8M28 16V5h3v11M3 24l6-4h9l-5 4h8l10-6"/></svg></div>
    <strong>Revenue Growth:</strong>+18% YoY
  </div>
  <div class="page-tab">Page 06 Of 08</div>
</section>

<!-- 07 Affiliates -->
<section class="slide col-right row-3">
  <div class="slide-title">Our Affiliates</div>
  <div class="affiliate" style="left:24px">
    <div class="name">TV Balance<br>Co.</div>
    <p>TV Balance Co. provides quality service, calibration, and installation of industrial scales to clients across Texas.</p>
    <p>You can also turn to us for new equipment sales and installation across the United States, Canada, and Mexico.</p>
  </div>
  <div class="affiliate" style="left:164px;padding-top:14px">
    <div class="name compact">Meadowlark Handling<br>&amp; Massing</div>
    <p>At Meadowlark Handling &amp; Massing, we hold ourselves to the highest standards of honesty and integrity. Our commitment to providing exceptional products and services goes above and beyond what our customers expect.</p>
    <p>We foster an environment of employee growth and job satisfaction, ensuring a safe and healthy workplace. Our goal is to achieve market dominance</p>
  </div>
  <div class="affiliate" style="left:304px">
    <div class="name">Fernway<br>Balance</div>
    <p>Fernway Balance was established in 2004 and proudly serves the midwest and west regions including colorado, wyoming, and iowa, offering the highest quality products and services to exceed your expectations.</p>
  </div>
  <div class="page-tab">Page 07 Of 08</div>
</section>

<!-- 08 Operational -->
<section class="slide col-right row-4">
  <div class="slide-title">Operational Performance</div>
  <div class="photo" role="img" aria-label="Engineers in hard hats monitoring a factory floor with data screens" style="left:25px;top:63px;width:203px;height:168px;background:linear-gradient(135deg,#9fb3c6,#3e5a78 50%,#1b2638)"></div>
  <div class="tick red pos" style="left:249px;top:84px;font-size:8.3px">Service Calls Completed: 2,350 YTD (+22%)</div>
  <div class="tick red pos" style="left:249px;top:110px;font-size:8.3px">Average Response Time: 1.8 hours</div>
  <div class="tick red pos" style="left:249px;top:136px;font-size:8.3px">Field Calibration Compliance: 99.8%</div>
  <div class="tick red pos" style="left:249px;top:161px;font-size:8.3px">Customer Satisfaction (NPS): 91%</div>
  <div class="tick red pos" style="left:249px;top:187px;font-size:8.3px;width:196px;line-height:13px">Include a bar or line chart visualizing quarterly trends</div>
  <div class="page-tab">Page 08 Of 08</div>
</section>

</body>
</html>
```